Moravel Aesthetic Doctor

I require an elegant, luxurious looking business card for my aesthetic business. I am a doctor and that will set me aside from competitors. I am planning to provide home and spa based treatments to clients with high expectations. I have attached my logo.

```html
<!DOCTYPE html>
<html lang="en">
<head>
<meta charset="utf-8">
<title>Moravel Aesthetic Doctor – Business Card</title>
<link rel="stylesheet" href="https://fonts.googleapis.com/css2?family=Raleway:wght@400;500&family=Roboto:ital,wght@0,300;0,400;1,400&display=swap">
<style>
  :root {
    --backdrop: #c4c4c4;
    --card: #f3f4f5;
    --ink: #2e3135;
    --steel: #8c929c;
    --sky: #4a9fd6;
    --sky-soft: #5aaee0;
    --navy: #1a67b0;
    --white: #ffffff;
  }
  * { margin: 0; padding: 0; box-sizing: border-box; }
  html, body {
    width: 1200px; height: 576px; overflow: hidden;
    background: var(--backdrop);
  }
  .card {
    position: absolute; top: 139px;
    width: 485px; height: 293px;
    background: var(--card);
    border-radius: 12px;
    overflow: hidden;
    box-shadow: 0 3px 6px rgba(0,0,0,.22);
    font-family: "Roboto", sans-serif;
  }
  .card--front { left: 81px; }
  .card--back  { left: 602px; }

  .brand { position: absolute; display: flex; align-items: center; }
  .brand__circle {
    border: 2px solid var(--steel);
    border-radius: 50%;
    flex: none;
  }
  .brand__name {
    font-family: "Raleway", sans-serif;
    font-weight: 400;
    color: var(--steel);
    line-height: 1;
    text-transform: uppercase;
  }
  .brand__name span { display: block; }

  .card--front .brand { left: 56px; top: 58px; }
  .card--front .brand__circle { width: 90px; height: 90px; margin-right: 16px; }
  .card--front .brand__main { font-size: 52px; letter-spacing: 1px; }
  .card--front .brand__sub { font-size: 20px; letter-spacing: 1.5px; margin-top: 6px; }

  .services {
    position: absolute; top: 194px; left: 0; right: 0;
    text-align: center; font-size: 13.5px; color: var(--ink);
    line-height: 19px;
  }
  .services .sep { color: var(--sky); margin: 0 7px; }

  .band {
    position: absolute; left: 0; right: 0; top: 239px; height: 33px;
    background: linear-gradient(90deg, var(--navy), #2c82c8 55%, var(--sky-soft));
    color: #e8f2fb;
    font-family: "Raleway", sans-serif; font-size: 13px; font-weight: 500;
    letter-spacing: 1px;
    display: flex; align-items: center; justify-content: center;
  }

  .person { position: absolute; left: 28px; top: 38px; }
  .person__name { font-size: 19px; font-weight: 400; color: var(--ink); }
  .person__letters { font-size: 10px; font-style: italic; color: var(--sky); margin-top: 4px; }
  .person__diploma { font-size: 13px; color: var(--sky); line-height: 16px; margin-top: 10px; }

  .card--back .brand { left: 215px; top: 38px; }
  .card--back .brand__circle { width: 68px; height: 68px; margin-right: 10px; }
  .card--back .brand__main { font-size: 38px; letter-spacing: 1px; }
  .card--back .brand__sub { font-size: 14.5px; letter-spacing: 1px; margin-top: 4px; }

  .contact {
    position: absolute; left: 28px; top: 158px;
    font-size: 12.5px; color: var(--ink); line-height: 19px;
  }
  .contact__row { display: flex; align-items: center; gap: 6px; }
  .contact__row + .contact__row { margin-top: 1px; }
  .contact__gap { margin-left: 14px; }
  .icon { width: 11px; height: 11px; fill: var(--sky); flex: none; }
  .social-dot {
    width: 12px; height: 12px; border-radius: 50%;
    background: var(--sky); display: inline-block; margin-left: 2px;
  }

  .wave { position: absolute; left: 0; top: 0; width: 485px; height: 293px; }
  .tagline {
    position: absolute; right: 22px; top: 229px;
    text-align: right; color: var(--white);
    font-family: "Raleway", sans-serif; font-size: 13px; line-height: 18px;
  }
</style>
</head>
<body>

<section class="card card--front">
  <div class="brand">
    <div class="brand__circle"></div>
    <div class="brand__name">
      <span class="brand__main">Moravel</span>
      <span class="brand__sub">Aesthetic Doctor</span>
    </div>
  </div>
  <div class="services">
    <div>Dermal Injectables<span class="sep">|</span>Plasma Facials<span class="sep">|</span>Microneedling</div>
    <div>Skin Boosters<span class="sep">|</span>Excessive Sweating</div>
  </div>
  <div class="band">HOME AND SPA BASED TREATMENTS</div>
</section>

<section class="card card--back">
  <svg class="wave" viewBox="0 0 485 293" aria-hidden="true">
    <path d="M0,238 C90,292 190,282 270,252 C350,222 410,200 485,198 L485,293 L0,293 Z" fill="var(--sky)"/>
    <path d="M0,222 C80,262 180,276 265,250 C345,226 410,178 485,176 L485,188 C410,192 345,236 265,262 C175,290 80,272 0,240 Z" fill="var(--steel)" opacity=".85"/>
    <path d="M40,244 C120,268 200,266 270,244 C340,222 400,194 485,190 L485,194 C400,200 340,230 270,252 C200,272 120,270 40,244 Z" fill="#b4bac2"/>
  </svg>

  <div class="person">
    <div class="person__name">Dr Elsa Varnik</div>
    <div class="person__letters">MRCPCH MD</div>
    <div class="person__diploma">Australasian Diploma of<br>Aesthetic Medicine</div>
  </div>

  <div class="brand">
    <div class="brand__circle"></div>
    <div class="brand__name">
      <span class="brand__main">Moravel</span>
      <span class="brand__sub">Aesthetic Doctor</span>
    </div>
  </div>

  <div class="contact">
    <div class="contact__row">
      <svg class="icon" viewBox="0 0 12 12"><path d="M0,2h12v8H0z M0,2l6,4.5L12,2" stroke="var(--card)" stroke-width="1"/></svg>
      <span>elsa@moravel.co.nz</span>
      <svg class="icon contact__gap" viewBox="0 0 12 12"><circle cx="6" cy="6" r="5.5"/><path d="M0.5,6h11M6,0.5v11" stroke="var(--card)" stroke-width="1"/></svg>
      <span>www.moravel.co.nz</span>
    </div>
    <div class="contact__row">
      <svg class="icon" viewBox="0 0 12 12"><path d="M2.5,0.5l2.2,2.6-1.3,1.6c.8,1.7,2.2,3.1,3.9,3.9l1.6-1.3,2.6,2.2-1.3,2C5,11,1,7,0.5,1.8z"/></svg>
      <span>0800 555 014</span>
    </div>
    <div class="contact__row">
      <span>Follow us on:</span>
      <span class="social-dot"></span><span class="social-dot"></span>
    </div>
  </div>

  <div class="tagline">Home and Spa<br>Based Treatments</div>
</section>

</body>
</html>
```